Travel Agency Website - Simple General

Need a 7 page simple design that is pretty repetitive. Need to be able to load quickly that is SEO optimized. Trying to give ideas on what they can do, be personal as we are local, but at the same time come across as professional and get information easily with little burden.

- Landing Page
- Brimwell Vacations Page
- Family Trips
- Road Trips from Texas
- Other Destinations
- About Us Page
- Contact Us Page

Target Market(s)

Families

Coding

Coded - Design and coding required

Number of Pages Required

5+ page

Colors

Designer to choose colors to be used in the design.

Requirements
Must have
• Like it to flow easily with our logo. Use that for colors, etc.

```html
<!DOCTYPE html>
<html lang="en">
<head>
<meta charset="utf-8">
<title>Meander &amp; Merry Travel Co. — Perfect Family Getaways</title>
<link rel="stylesheet" href="https://fonts.googleapis.com/css2?family=Outfit:wght@400;500;600;700&display=swap">
<style>
:root{
  --teal:#2f7f80;
  --teal-deep:#1f5f63;
  --teal-soft:rgba(55,135,135,.88);
  --gold:#c0924a;
  --gold-dark:#a97a35;
  --cream:#f8f3ea;
  --nav-text:#1f5f63;
  --white:#ffffff;
  --sky-top:#3d7fc9;
  --sky-mid:#9cc4e8;
  --snow:#eef3f8;
}
*{box-sizing:border-box;margin:0;padding:0}
html,body{width:1200px;height:1032px;overflow:hidden;background:var(--white);font-family:"Outfit",sans-serif}
.page{position:relative;width:1200px;height:1032px;overflow:hidden}
.hero-scene{position:absolute;left:0;top:0;width:1200px;height:782px;
  background:linear-gradient(180deg,var(--sky-top) 0%,var(--sky-mid) 38%,#d7e6f3 60%,var(--snow) 80%,#f7f9fc 100%)}
.hero-scene::after{content:"";position:absolute;left:440px;top:180px;width:720px;height:560px;border-radius:300px 300px 40px 40px;
  background:radial-gradient(ellipse at 50% 45%,rgba(220,60,150,.55),rgba(40,100,160,.45) 55%,rgba(90,70,90,.25) 80%,transparent 100%)}
.topbar{position:absolute;top:20px;left:82px;right:82px;display:flex;justify-content:space-between;color:var(--white);font-size:14px}
.topbar span{display:flex;align-items:center;gap:8px}
.topbar .dot{width:28px;height:28px;border-radius:50%;background:var(--white);display:flex;align-items:center;justify-content:center}
.topbar .phone{font-size:16px}
.nav{position:absolute;left:49px;top:66px;width:1099px;height:60px;background:var(--cream);border-radius:30px;display:flex;align-items:center;padding:0 28px 0 30px;font-size:16px;color:var(--nav-text)}
.nav a{color:inherit;text-decoration:none}
.nav .left{display:flex;gap:24px;align-items:center}
.nav .right{margin-left:auto;display:flex;gap:36px;align-items:center}
.btn{display:inline-flex;align-items:center;gap:12px;background:var(--gold);color:var(--white);border-radius:22px;font-weight:500;text-decoration:none}
.btn .arrow{width:28px;height:28px;border-radius:50%;background:var(--gold-dark);display:flex;align-items:center;justify-content:center}
.nav .btn{height:38px;padding:0 6px 0 27px;font-size:15px;margin-left:0}
.brand{position:absolute;left:506px;top:16px;width:188px;height:172px;background:var(--cream);border:3px solid #a9d3cd;border-radius:46px;display:flex;flex-direction:column;align-items:center;justify-content:center;color:var(--teal-deep);font-weight:600;text-align:center;line-height:1}
.brand .name{font-size:30px}
.brand .sub{font-size:11px;letter-spacing:2px;margin-top:10px}
.offer{position:absolute;left:70px;top:228px;width:450px;height:412px;background:var(--teal-soft);border-radius:90px 90px 90px 90px;color:var(--white);text-align:center;padding-top:110px}
.offer::before{content:"";position:absolute;inset:12px;border:1.5px solid rgba(255,255,255,.45);border-radius:80px}
.offer h1{font-size:40px;font-weight:700;line-height:1.02;letter-spacing:.5px}
.offer p{font-size:16.5px;line-height:1.22;margin:20px auto 0;width:300px}
.offer .btn{margin-top:22px;height:40px;padding:0 6px 0 24px;font-size:13.5px;font-weight:700;letter-spacing:.3px}
.spark{position:absolute}
.tiles{position:absolute;top:722px;left:78px;display:flex;gap:12px}
.tile{position:relative;width:250px;height:222px;border-radius:60px;overflow:hidden;display:flex;align-items:flex-end;justify-content:center;padding-bottom:36px}
.tile.active{border:5px solid var(--gold)}
.tile span{position:relative;color:var(--white);font-weight:700;font-size:18px;line-height:1.05;text-align:center;letter-spacing:.3px}
.tile::after{content:"";position:absolute;inset:0;background:linear-gradient(180deg,transparent 45%,rgba(25,80,90,.85))}
.tile span{z-index:1}
.t1{background:linear-gradient(180deg,#1d6fd8,#4f8fd0 60%,#3a6e5a)}
.t2{background:linear-gradient(160deg,#5b8fd0,#c2409a 55%,#2e6c98)}
.t3{background:linear-gradient(180deg,#f0a860,#e78a55 35%,#4c6b3c 60%,#555a60)}
.t4{background:linear-gradient(180deg,#c0542a,#d57738 40%,#9bb2c6 75%)}
.footer{position:absolute;left:0;top:970px;width:1200px;height:62px;background:var(--cream);display:flex;align-items:center;justify-content:center;font-size:14px;color:#2a3a3c}
.social{position:absolute;right:107px;top:985px;display:flex;gap:8px}
.social span{width:24px;height:24px;border-radius:50%;background:var(--teal-deep)}
</style>
</head>
<body>
<div class="page">
  <div class="hero-scene" role="img" aria-label="Photo of a smiling family in bright ski jackets sitting in the snow with skis, snowy mountains and blue sky behind"></div>

  <div class="topbar">
    <span><i class="dot"><svg width="14" height="10" viewBox="0 0 14 10"><rect x=".5" y=".5" width="13" height="9" rx="1" fill="none" stroke="#3d7fc9"/><path d="M1 1l6 5 6-5" fill="none" stroke="#3d7fc9"/></svg></i>hello@meanderandmerry.com</span>
    <span class="phone"><i class="dot"><svg width="14" height="14" viewBox="0 0 24 24"><path fill="#3d7fc9" d="M6.6 10.8a15 15 0 006.6 6.6l2.2-2.2c.3-.3.7-.4 1-.2 1.1.4 2.3.6 3.6.6.6 0 1 .4 1 1V20c0 .6-.4 1-1 1A17 17 0 013 4c0-.6.4-1 1-1h3.5c.6 0 1 .4 1 1 0 1.3.2 2.5.6 3.6.1.3 0 .7-.2 1z"/></svg></i>Phone Number (123) 456 7890</span>
  </div>

  <nav class="nav">
    <div class="left">
      <svg width="14" height="14" viewBox="0 0 14 14"><path fill="#c0924a" d="M7 1l6 5.5h-2V13H8.5V9h-3v4H3V6.5H1z"/></svg>
      <a href="#">Brimwell Vacations</a><a href="#">Family Trips</a><a href="#">Texas Road Trips</a>
    </div>
    <div class="right">
      <a href="#">Other Destinations</a><a href="#">About Us</a>
      <a class="btn" href="#">Contact Us <i class="arrow"><svg width="10" height="10" viewBox="0 0 10 10"><path d="M2 8l6-6M3 2h5v5" stroke="#fff" fill="none" stroke-width="1.4"/></svg></i></a>
    </div>
  </nav>

  <div class="brand"><span class="name">Meander<br>&amp; Merry</span><span class="sub">TRAVEL CO.</span></div>

  <section class="offer">
    <svg class="spark" style="left:185px;top:45px" width="90" height="50" viewBox="0 0 90 50"><path fill="#fff" d="M45 0l3 18 14 3-14 3-3 18-3-18-14-3 14-3zM10 26l1.5 7 6 1.5-6 1.5L10 43l-1.5-7-6-1.5 6-1.5zM80 22l1.5 7 6 1.5-6 1.5L80 39l-1.5-7-6-1.5 6-1.5z"/></svg>
    <svg class="spark" style="left:392px;top:240px" width="24" height="30" viewBox="0 0 24 30"><path fill="#fff" d="M12 0l2 13 10 2-10 2-2 13-2-13L0 15l10-2z"/></svg>
    <svg class="spark" style="left:96px;top:382px" width="20" height="26" viewBox="0 0 24 30"><path fill="#fff" d="M12 0l2 13 10 2-10 2-2 13-2-13L0 15l10-2z"/></svg>
    <h1>PERFECT FAMILY<br>GETAWAYS</h1>
    <p>Stress-free, fun-filled vacations designed for all ages—because every family deserves time together.</p>
    <a class="btn" href="#">PLAN FAMILY TRIP <i class="arrow"><svg width="10" height="10" viewBox="0 0 10 10"><path d="M2 8l6-6M3 2h5v5" stroke="#fff" fill="none" stroke-width="1.4"/></svg></i></a>
  </section>

  <div class="tiles">
    <a class="tile t1" role="img" aria-label="Photo of a fairytale castle under a blue sky"><span>BRIMWELL VACATIONS<br>LAND AND SEA</span></a>
    <a class="tile t2 active" role="img" aria-label="Photo of a family in ski gear in the snow"><span>FAMILY<br>TRIPS</span></a>
    <a class="tile t3" role="img" aria-label="Photo of an open Texas highway at sunset with a water tower"><span>TEXAS<br>ROAD TRIPS</span></a>
    <a class="tile t4" role="img" aria-label="Photo of hikers beneath a red rock arch"><span>OTHER<br>DESTINATIONS</span></a>
  </div>

  <footer class="footer">© 2026 Meander &amp; Merry. All Right Reserved</footer>
  <div class="social"><span aria-label="Social profile"></span><span aria-label="Social profile"></span></div>
</div>
</body>
</html>
```